Clear Path Keystone Realty yard sign Logo

UPDATE Design logo for Realty yard sign. 24x24 diamond or 36x24 Rectangle.
Open to all ideas. We are a discount firm but want to project a high end feel. We provide 100% of all services and extensive marketing for 1/2 the fee.
The following info must be on sign
CLEAR PATH KEYSTONE (OR K) REALTY
Doran Pike 547-6093
KeystonePX.com

Target Market(s)

home sellers and buyers

Industry/Entity Type

Real Estate yard sign please see sign attached in gif

Logo Text

Clear Path Keystone Realty OR (K IN PLACE OF KEYSTONE)

Requirements
Must have
• CLEAR PATH KEYSTONE (OR K) REALTY Doran Pike 547-6093 KeystonePX.com FOR SALE (optional)

```html
<!DOCTYPE html>
<html lang="en">
<head>
<meta charset="utf-8">
<title>Clear Path Keystone Realty – Yard Sign</title>
<link rel="stylesheet" href="https://fonts.googleapis.com/css2?family=Fraunces:opsz,wght@144,900&family=Arimo:wght@700&display=swap">
<style>
  :root {
    --page: #eef0f2;
    --sign-sky: #3bb3fe;
    --frame-blue: #0457ec;
    --banner-deep: #f24c0c;
    --banner-orange: #fd7724;
    --brand-orange: #f77a2b;
    --text-white: #ffffff;
  }
  html, body {
    margin: 0;
    padding: 0;
    width: 1200px;
    height: 1199px;
    overflow: hidden;
    background: var(--page);
  }
  .yard-sign {
    position: absolute;
    left: 20px;
    top: 213px;
    width: 1160px;
    height: 772px;
    display: block;
  }
  .sign-board { fill: var(--sign-sky); }
  .frame-outer { fill: var(--frame-blue); }
  .frame-inner { fill: var(--sign-sky); }
  .banner-edge { fill: var(--banner-deep); }
  .banner-face { fill: var(--banner-orange); }
  .for-sale {
    font-family: "Fraunces", Georgia, serif;
    font-weight: 900;
    font-size: 112px;
    fill: var(--text-white);
    letter-spacing: 1px;
  }
  .brand-name {
    font-family: "Fraunces", Georgia, serif;
    font-weight: 900;
    fill: var(--brand-orange);
  }
  .brand-main { font-size: 128px; }
  .brand-sub { font-size: 64px; letter-spacing: 2px; }
  .agent-line {
    font-family: "Arimo", Arial, sans-serif;
    font-weight: 700;
    font-size: 54px;
    fill: var(--text-white);
  }
  .web-address {
    font-family: "Arimo", Arial, sans-serif;
    font-weight: 700;
    font-size: 64px;
    fill: var(--text-white);
  }
</style>
</head>
<body>
  <svg class="yard-sign" viewBox="0 0 1346 896" role="img" aria-label="Clear Path Keystone Realty for sale yard sign">
    <rect class="sign-board" x="0" y="0" width="1346" height="896"/>

    <path class="frame-outer" d="M70 50 L1215 103 Q1300 110 1296 190 L1252 665 Q1240 722 1157 728 L300 818 Q160 835 137 760 L45 150 Q35 60 110 50 Z"/>
    <path class="frame-inner" d="M175 122 L1150 146 Q1188 150 1188 240 L1195 615 Q1193 685 1100 690 L330 745 Q250 750 230 690 L118 200 Q108 125 175 122 Z"/>

    <path class="banner-edge" d="M268 88 L1123 90 L1057 220 L400 282 Z"/>
    <path class="banner-face" d="M305 102 L1098 104 L1045 206 L418 262 Z"/>
    <text class="for-sale" x="708" y="205" text-anchor="middle">FOR SALE</text>

    <text class="brand-name brand-main" x="690" y="445" text-anchor="middle">Clear Path</text>
    <text class="brand-name brand-sub" x="690" y="545" text-anchor="middle">Keystone Realty</text>

    <text class="agent-line" x="443" y="682">Doran Pike 547-6093</text>
    <text class="web-address" x="1290" y="856" text-anchor="end">KeystonePX.com</text>
  </svg>
</body>
</html>
```